need corporate, modern business card created for Consulting Company

I need a slick business card using elements from my website, as well as, integrating my pixelforge-created logo (see files).

The business card needs to be:
1. Corporate and modern
2. Clean and professional

I've included a PSD with the logo/icon that you can use to create it. Feel free to try a metallic finish on the logo, make it bigger/small, underlay it. Whatever you need to do to make my card stand out.

Try a black background, or white background or gray.

The idea is for my card to be memorable as well as professional and corporate.

Target Market(s)

Corporate business in the US and Canada.

Industry/Entity Type

Business

Contact Information for Business Card

Commerce Advancing Methods
Martin Coles, Senior Partner
office: 1 877 555 0143
mobile: 1 519 555 0172
website: http://www.brightvale.example

Requirements
Must have
• Card-related information
• corporate, yet modern
• clean and professional
• incorporate the icon only
• must have an editable form when complete!
Nice to have
• metallic icon might be cool
• try it with white or black

```html
<!DOCTYPE html>
<html lang="en">
<head>
<meta charset="utf-8">
<title>Brightvale Business Card</title>
<link rel="stylesheet" href="https://fonts.googleapis.com/css2?family=Source+Sans+3:wght@400;600;700&display=swap">
<style>
  :root {
    --bg: #e9e7e3;
    --ink-dark: #141517;
    --ink-mid: #2a2c30;
    --blue: #2f7fc0;
    --blue-light: #4aa0d8;
    --white: #ffffff;
    --paper: #f4f4f4;
    --text-light: #f2f2f2;
    --text-dark: #2b2b2d;
    --rule: #9a9a9a;
  }
  * { margin: 0; padding: 0; box-sizing: border-box; }
  html, body { width: 1200px; height: 902px; overflow: hidden; }
  body {
    background: var(--bg);
    font-family: "Source Sans 3", sans-serif;
    position: relative;
  }
  .card {
    position: absolute;
    width: 540px;
    height: 308px;
    overflow: hidden;
    box-shadow: 0 6px 18px rgba(0,0,0,0.18);
  }
  .card-front {
    left: 60px; top: 100px;
    background: linear-gradient(135deg, var(--ink-mid) 0%, var(--ink-dark) 70%);
    color: var(--text-light);
  }
  .card-back {
    left: 600px; top: 494px;
    background: var(--paper);
  }
  .corner-shapes { position: absolute; inset: 0; width: 100%; height: 100%; }

  .brand { position: absolute; display: flex; flex-direction: column; }
  .brand-row { display: flex; align-items: center; gap: 10px; }
  .brand-mark { width: 14px; height: 14px; background: var(--blue); }
  .brand-name { font-weight: 700; color: var(--blue-light); line-height: 1; }
  .brand-tagline { font-weight: 400; }

  .card-front .brand { left: 34px; top: 44px; }
  .card-front .brand-name { font-size: 38px; }
  .card-front .brand-tagline { font-size: 14px; margin-left: 24px; color: var(--text-light); }

  .person { position: absolute; left: 58px; top: 178px; text-align: right; width: 190px; }
  .person-name { font-size: 27px; font-weight: 600; line-height: 1.1; }
  .person-role { font-size: 14px; }

  .divider { position: absolute; left: 268px; top: 96px; width: 1px; height: 150px; background: var(--rule); }

  .contact { position: absolute; left: 284px; top: 98px; list-style: none; font-size: 13px; line-height: 1.35; }
  .contact li { display: flex; gap: 9px; align-items: flex-start; margin-bottom: 4px; }
  .contact svg { flex: 0 0 12px; width: 12px; height: 12px; margin-top: 2px; fill: var(--text-light); }

  .card-back .brand { left: 0; right: 0; top: 118px; align-items: center; }
  .card-back .brand-name { font-size: 54px; color: var(--blue); }
  .card-back .brand-mark { width: 18px; height: 18px; }
  .card-back .brand-tagline { font-size: 16px; color: var(--text-dark); margin-left: 40px; }
</style>
</head>
<body>

<section class="card card-front" aria-label="Card front">
  <svg class="corner-shapes" viewBox="0 0 540 308" preserveAspectRatio="none">
    <defs>
      <linearGradient id="blueFade" x1="0" y1="0" x2="1" y2="1">
        <stop offset="0" stop-color="#2a76b8"/>
        <stop offset="1" stop-color="#5aaee0"/>
      </linearGradient>
    </defs>
    <polygon points="360,0 540,0 540,120" fill="url(#blueFade)"/>
    <line x1="360" y1="0" x2="540" y2="120" stroke="#d9dde2" stroke-width="2"/>
    <polygon points="0,190 0,308 178,308" fill="url(#blueFade)"/>
    <line x1="0" y1="190" x2="178" y2="308" stroke="#d9dde2" stroke-width="2"/>
  </svg>

  <div class="brand">
    <div class="brand-row">
      <span class="brand-mark"></span>
      <span class="brand-name">brightvale</span>
    </div>
    <span class="brand-tagline">Commerce Advancing Methods</span>
  </div>

  <div class="person">
    <p class="person-name">Martin Coles</p>
    <p class="person-role">Senior Partner</p>
  </div>

  <span class="divider"></span>

  <ul class="contact">
    <li><svg viewBox="0 0 12 12"><path d="M2 1h2.5l1 3-1.5 1a6 6 0 0 0 3 3l1-1.5 3 1V11c-5 0-9-4-9-9z"/></svg>1 877 555 0143</li>
    <li><svg viewBox="0 0 12 12"><path d="M3 0h6v12H3zM4 1.5v8h4v-8z"/></svg>1 519 555 0172</li>
    <li><svg viewBox="0 0 12 12"><path d="M6 0a4 4 0 0 1 4 4c0 3-4 8-4 8S2 7 2 4a4 4 0 0 1 4-4zm0 2.5a1.5 1.5 0 1 0 0 3 1.5 1.5 0 0 0 0-3z"/></svg>48 Harbour Lane Suite 310,<br>Kingsford, Ontario, K7L 2B4</li>
    <li><svg viewBox="0 0 12 12"><path d="M0 1h12v8H7v1.5h2V12H3v-1.5h2V9H0zm1 1v6h10V2z"/></svg>www.brightvale.example</li>
    <li><svg viewBox="0 0 12 12"><path d="M0 2h12v8H0zm1 1v.4l5 3.2 5-3.2V3z"/></svg>info@brightvale.example</li>
  </ul>
</section>

<section class="card card-back" aria-label="Card back">
  <svg class="corner-shapes" viewBox="0 0 540 308" preserveAspectRatio="none">
    <polygon points="0,0 58,0 0,118" fill="#2f7fc0"/>
    <line x1="58" y1="0" x2="0" y2="118" stroke="#1b1c1f" stroke-width="2.5"/>
    <polygon points="540,190 540,308 482,308" fill="#2f7fc0"/>
    <line x1="540" y1="190" x2="482" y2="308" stroke="#1b1c1f" stroke-width="2.5"/>
  </svg>

  <div class="brand">
    <div class="brand-row">
      <span class="brand-mark"></span>
      <span class="brand-name">brightvale</span>
    </div>
    <span class="brand-tagline">Commerce Advancing Methods</span>
  </div>
</section>

</body>
</html>
```